Creative, fresh business card design for Ripplecraft Facades

We need a fresh, creative business card design for Ripplecraft Facades. We are the manufacturer of Ripplecraft Facades in Australia. Wall panels are 2400 x 1200mm panels made from MDF and feature 3D patterns on the face of the panel. The colours to be used are green, silver/grey and white RGB
Red 187
Green 207
Blue 65.

An idea is to possibly use a watermark of one of our designs as a background (like on the "Grids" design on the left hand side of page 2 of our brochure).

Target Market(s)

Interior designers, architects, builders and home renovators

Industry/Entity Type

Business

Contact Information for Business Card

Details to go on the card are:
Our logo (attached),
Slogan: "Decorative panels for interiors and exteriors",
Contact name,
Position,
Mobile phone number,
Business address,
Business phone,
Business fax,
Website and
Email address.

I have attached a few images of our panels and our brochure for reference.

The colours of the business card should feature our logo colours which are: RGB
Red 187
Green 207
Blue 65

Requirements
Must have
• Very modern fonts and design. Some of the designs shown especially the "Prisms" design which is a popular design.
Nice to have
• Creative but simple design. Very contemporary.
Should not have
• Anything ornate or old fashioned.

```html
<!DOCTYPE html>
<html lang="en">
<head>
<meta charset="utf-8">
<title>Ripplecraft Facades – Business Card</title>
<link href="https://fonts.googleapis.com/css2?family=Open+Sans:wght@400;600;700&display=swap" rel="stylesheet">
<style>
  :root {
    --backdrop: #1b1b1c;
    --card: #3a3a3c;
    --card-deep: #2e2e30;
    --lime: #bbcf41;
    --silver: #a7a8ab;
    --white: #ffffff;
    --text-soft: #d9d9da;
  }
  * { box-sizing: border-box; margin: 0; padding: 0; }
  html, body {
    width: 1200px; height: 1000px; overflow: hidden;
    background: var(--backdrop);
    font-family: "Open Sans", Arial, sans-serif;
  }
  .stage {
    position: relative; width: 1200px; height: 1000px;
    display: flex; align-items: center; justify-content: center;
  }
  .card {
    position: relative; width: 860px; height: 500px;
    border-radius: 36px; overflow: hidden;
    background: linear-gradient(135deg, var(--card) 0%, #404042 45%, var(--card-deep) 100%);
  }
  .card__watermark {
    position: absolute; right: -40px; top: 150px;
    width: 380px; height: 380px;
    background: rgba(0,0,0,0.12);
    border-radius: 10px;
  }
  .brand {
    position: absolute; right: 48px; top: 44px;
    text-align: right;
  }
  .brand__row { display: flex; align-items: center; justify-content: flex-end; gap: 14px; }
  .brand__square { width: 44px; height: 44px; background: var(--lime); }
  .brand__name {
    font-weight: 700; font-size: 30px; color: var(--lime); letter-spacing: 0.5px;
  }
  .brand__slogan {
    margin-top: 12px; font-size: 15px; line-height: 1.25;
    color: var(--silver); letter-spacing: 3px;
  }
  .accent { position: absolute; left: 0; width: 12px; }
  .accent--title { top: 270px; height: 60px; background: var(--lime); }
  .accent--address { top: 336px; height: 60px; background: var(--lime); }
  .accent--contact { top: 402px; height: 98px; background: var(--silver); }
  .person { position: absolute; left: 40px; top: 268px; }
  .person__name {
    font-weight: 700; font-size: 34px; color: var(--white); letter-spacing: 0.5px; line-height: 1;
  }
  .person__role {
    margin-top: 8px; font-size: 18px; font-weight: 600; color: var(--lime); letter-spacing: 0.5px;
  }
  .address {
    position: absolute; left: 40px; top: 340px;
    font-size: 18px; line-height: 1.3; color: var(--text-soft);
  }
  .contacts { position: absolute; left: 40px; top: 400px; list-style: none; }
  .contacts li {
    display: flex; align-items: center; gap: 18px;
    height: 19px; font-size: 16px; color: var(--text-soft);
  }
  .contacts svg { width: 14px; height: 14px; flex: none; }
  .contacts .lime { color: var(--lime); }
</style>
</head>
<body>
<main class="stage">
  <section class="card" aria-label="Ripplecraft Facades business card">
    <div class="card__watermark" aria-hidden="true"></div>

    <header class="brand">
      <div class="brand__row">
        <span class="brand__square" aria-hidden="true"></span>
        <span class="brand__name">Ripplecraft Facades</span>
      </div>
      <p class="brand__slogan">decorative panels for<br>interiors &amp; landscapes</p>
    </header>

    <span class="accent accent--title"></span>
    <span class="accent accent--address"></span>
    <span class="accent accent--contact"></span>

    <div class="person">
      <h1 class="person__name">DANA WHITLOW</h1>
      <p class="person__role">CEO &amp; FOUNDER</p>
    </div>

    <p class="address">18 Kestrel Lane,<br>Marlow Bay, 40512</p>

    <ul class="contacts">
      <li>
        <svg viewBox="0 0 14 14" aria-hidden="true"><rect x="3.5" y="1" width="7" height="12" rx="1.5" fill="none" stroke="#bbcf41" stroke-width="1.5"/><circle cx="7" cy="11" r="0.8" fill="#bbcf41"/></svg>
        <span>+61 400 555 210</span>
      </li>
      <li>
        <svg viewBox="0 0 14 14" aria-hidden="true"><path d="M3 1.5l2.5 2.8-1.3 1.6c.9 1.7 2.2 3 3.9 3.9l1.6-1.3 2.8 2.5-1.5 1.8C6 12.5 1.5 8 .9 3z" fill="#bbcf41"/></svg>
        <span>+61 2 5550 1842</span>
      </li>
      <li>
        <svg viewBox="0 0 14 14" aria-hidden="true"><rect x="4" y="1" width="7" height="4" fill="#bbcf41"/><rect x="1" y="5" width="12" height="7" rx="1" fill="#bbcf41"/><rect x="4" y="8" width="6" height="1.2" fill="#3a3a3c"/></svg>
        <span>+61 2 5550 1843</span>
      </li>
      <li>
        <svg viewBox="0 0 14 14" aria-hidden="true"><rect x="1" y="3" width="12" height="8.5" fill="#bbcf41"/><path d="M1 3l6 5 6-5" fill="none" stroke="#3a3a3c" stroke-width="1.2"/></svg>
        <span>dana@ripplecraftfacades.com</span>
      </li>
      <li>
        <svg viewBox="0 0 14 14" aria-hidden="true"><circle cx="8" cy="6" r="4" fill="none" stroke="#bbcf41" stroke-width="1.8"/><path d="M5.2 8.8L1.5 12.5" stroke="#bbcf41" stroke-width="2"/></svg>
        <span>www.<span class="lime">ripplecraftfacades</span>.com</span>
      </li>
    </ul>
  </section>
</main>
</body>
</html>
```